Roofing company in Toronto, Canada needs a logo design and business card design

We need a business card and logo created for our company. Our company is "KLV Roofing" which provides roofing services for commercial and residential customers. We serve customers in the Greater Toronto Area (in Canada) thus the name KLV.

We want the logo and business card to be a modern design displaying professionalism and quality in the work. We would prefer rounded corners for the business cards but are open to other ideas. The cards should be pleasant and appealing to customers.

Target Market(s)

Commercial and Residential customers

Industry/Entity Type

Roofing

Contact Information for Business Card

Logo Text

KLV Roofing

Requirements
Nice to have
• Colours that are pleasing to the eye but at the same time should stand out from other business cards. If the design can incorporate the name of KLV Roofing and the actual concept of roofing that would be nice.
Should not have
• Do not want the business cards or logo to be childish looking. Need to look professionally designed.

```html
<!DOCTYPE html>
<html lang="en">
<head>
<meta charset="utf-8">
<title>KLV Roofing – Business Card</title>
<link rel="stylesheet" href="https://fonts.googleapis.com/css2?family=Orbitron:wght@700&family=Source+Sans+3:wght@400;600&display=swap">
<style>
  :root {
    --backdrop: #b9b9b9;
    --card-light: #f2f2f2;
    --brand-blue: #1a72c2;
    --brand-grey: #7d7d7d;
    --ink: #333333;
    --white: #ffffff;
    --tint-light-a: rgba(26, 114, 194, 0.0);
    --tint-light-b: rgba(26, 114, 194, 0.12);
    --tint-blue-a: rgba(255, 255, 255, 0.0);
    --tint-blue-b: rgba(255, 255, 255, 0.10);
  }
  * { box-sizing: border-box; margin: 0; padding: 0; }
  html, body { width: 1200px; height: 900px; overflow: hidden; }
  body {
    background: var(--backdrop);
    position: relative;
    font-family: "Source Sans 3", Arial, sans-serif;
  }
  .card {
    position: absolute;
    top: 170px;
    width: 347px;
    height: 561px;
    overflow: hidden;
  }
  .card--front { left: 259px; background: var(--card-light); }
  .card--back { left: 631px; background: var(--brand-blue); }

  .card__backdrop {
    position: absolute;
    left: 0; right: 0; bottom: 0;
  }
  .card--front .card__backdrop {
    top: 275px;
    background: linear-gradient(180deg, var(--tint-light-a), var(--tint-light-b));
  }
  .card--back .card__backdrop {
    top: 330px;
    background: linear-gradient(180deg, var(--tint-blue-a), var(--tint-blue-b));
  }

  .wordmark {
    position: absolute;
    left: 0; right: 0;
    text-align: center;
    font-family: "Orbitron", Arial, sans-serif;
    font-weight: 700;
    line-height: 1;
  }
  .wordmark__main { display: block; font-size: 58px; letter-spacing: 1px; }
  .wordmark__sub { display: block; font-size: 31px; letter-spacing: 2px; margin-top: 10px; }
  .card--front .wordmark { top: 112px; color: var(--brand-blue); }
  .card--back .wordmark { top: 222px; color: var(--white); }

  .contact {
    position: absolute;
    left: 0; right: 0;
    top: 343px;
    text-align: center;
    color: var(--ink);
    font-size: 15px;
    line-height: 21px;
  }
  .contact__name {
    font-family: "Orbitron", Arial, sans-serif;
    font-weight: 700;
    font-size: 20px;
    letter-spacing: 1px;
    color: var(--brand-blue);
    line-height: 24px;
  }
  .contact__role { margin-bottom: 20px; }
  .contact__label { color: var(--brand-blue); font-weight: 600; }
  .contact__web { color: var(--brand-blue); font-weight: 600; margin-bottom: 9px; }
  .contact__address { line-height: 18px; }
</style>
</head>
<body>
  <section class="card card--front">
    <div class="card__backdrop" role="img" aria-label="Faint rooftop and house silhouette decoration"></div>
    <div class="wordmark">
      <span class="wordmark__main">KLV</span>
      <span class="wordmark__sub">ROOFING</span>
    </div>
    <div class="contact">
      <p class="contact__name">JOHN SMITH</p>
      <p class="contact__role">Managing Director</p>
      <p><span class="contact__label">P:</span> 823-456-7890</p>
      <p><span class="contact__label">E:</span> info@youremail.com</p>
      <p class="contact__web">www.websitename.com</p>
      <p class="contact__address">1234, Address Goes Here<br>Country Name, 123456</p>
    </div>
  </section>

  <section class="card card--back">
    <div class="card__backdrop" role="img" aria-label="Faint rooftop and house silhouette decoration"></div>
    <div class="wordmark">
      <span class="wordmark__main">KLV</span>
      <span class="wordmark__sub">ROOFING</span>
    </div>
  </section>
</body>
</html>
```